Logo for a Food & Beverage Franchise Company

We need a logo and stationary for a new company that just aquired a restaurant franchise. We need a sleep and professional logo with stationary.

Target Market(s)

Adults, resturaunt owners, franchisors (Companies who own food franchise companies such as Farrowbys Head Office, Toastwell International Franchise)
and Big Food and Beverage who wish to give franchise rights to us)

Industry/Entity Type

Restaurant

Logo Text

Velvet Harbor

Logo styles of interest
Emblem Logo
Pictorial/Combination Logo
Character Logo
Font styles to use
Serif
Sans Serif

Colors
ffc214
f78f20
f37022
faa54b
fece3e
fbed22

Requirements
Must have
• Maximum three color. The less the better.
Nice to have
• It does not have to have a crown, but if you wish to have a crown then it does not have to be so sharp and clear. Abstract is better.

```html
<!DOCTYPE html>
<html lang="en">
<head>
<meta charset="utf-8">
<title>Velvet Harbor — Stationery Set</title>
<link rel="stylesheet" href="https://fonts.googleapis.com/css2?family=Josefin+Sans:wght@400;600&family=Open+Sans:wght@400;600&display=swap">
<style>
  :root {
    --backdrop: #535d68;
    --orange: #fb9a00;
    --orange-soft: #fcb547;
    --yellow: #fdd421;
    --paper: #ffffff;
    --ink: #2a2a2a;
    --brand-font: "Josefin Sans", Arial, sans-serif;
    --body-font: "Open Sans", Arial, sans-serif;
  }
  * { box-sizing: border-box; margin: 0; padding: 0; }
  html, body { width: 1200px; height: 900px; overflow: hidden; }
  body { background: var(--backdrop); font-family: var(--body-font); }
  .canvas { position: relative; width: 1200px; height: 900px; background: var(--backdrop); }

  .brand-name {
    font-family: var(--brand-font);
    font-weight: 600;
    text-transform: uppercase;
    letter-spacing: 0.18em;
    white-space: nowrap;
  }
  .brand-lockup { display: flex; align-items: center; gap: 8px; }
  .brand-square { display: block; background: currentColor; }

  /* Report cover */
  .cover {
    position: absolute; left: 60px; top: 60px; width: 310px; height: 430px;
    background: var(--orange); box-shadow: 0 6px 14px rgba(0,0,0,.25);
  }
  .cover__band {
    height: 92px; background: var(--paper); color: var(--orange);
    display: flex; align-items: center; justify-content: center;
  }
  .cover__band .brand-name { font-size: 13px; }
  .cover__band .brand-square { width: 10px; height: 10px; }
  .cover__body {
    height: 338px; display: flex; flex-direction: column; align-items: center; justify-content: center; gap: 18px;
    color: var(--paper);
  }
  .cover__body .brand-square { width: 90px; height: 90px; }
  .cover__body .brand-name { font-size: 22px; }

  /* Letterhead */
  .letterhead {
    position: absolute; left: 410px; top: 60px; width: 310px; height: 430px;
    background: var(--paper); box-shadow: 0 6px 14px rgba(0,0,0,.25);
    padding: 26px 26px 20px;
  }
  .letterhead__header { display: flex; justify-content: flex-end; color: var(--orange); margin-bottom: 22px; }
  .letterhead__header .brand-name { font-size: 10px; }
  .letterhead__header .brand-square { width: 8px; height: 8px; }
  .letterhead__body p {
    font-size: 7px; line-height: 1.5; color: var(--ink); text-align: justify; margin-bottom: 7px;
  }
  .letterhead__footer { position: absolute; left: 26px; bottom: 20px; color: var(--orange); }
  .letterhead__footer .brand-name { font-size: 8px; }

  /* Disc */
  .disc {
    position: absolute; left: 790px; top: 110px; width: 320px; height: 320px; border-radius: 50%;
    background: var(--orange); box-shadow: 0 6px 14px rgba(0,0,0,.25); color: var(--paper);
  }
  .disc__hub {
    position: absolute; left: 50%; top: 50%; width: 74px; height: 74px; margin: -37px 0 0 -37px;
    border-radius: 50%; background: #8f949a; border: 10px solid #c9ccd0;
  }
  .disc__hole {
    position: absolute; left: 50%; top: 50%; width: 26px; height: 26px; margin: -13px 0 0 -13px;
    border-radius: 50%; background: var(--backdrop);
  }
  .disc__label { position: absolute; left: 0; right: 0; top: 68px; text-align: center; }
  .disc__label .brand-name { font-size: 14px; }
  .disc__mark { position: absolute; left: 50%; bottom: 62px; width: 22px; height: 22px; margin-left: -11px; background: var(--paper); }

  /* Envelope */
  .envelope { position: absolute; left: 60px; top: 570px; width: 540px; height: 270px; }
  .envelope__back {
    position: absolute; left: 16px; top: -18px; width: 540px; height: 270px;
    background: var(--yellow); box-shadow: 0 6px 14px rgba(0,0,0,.25);
  }
  .envelope__front {
    position: absolute; inset: 0;
    background: linear-gradient(160deg, var(--paper) 0 40%, var(--orange) 40% 100%);
    box-shadow: 0 6px 14px rgba(0,0,0,.25);
  }
  .envelope__name { position: absolute; left: 26px; top: 24px; color: var(--orange); }
  .envelope__name .brand-name { font-size: 13px; }
  .envelope__mark { position: absolute; right: 30px; top: 120px; width: 26px; height: 26px; background: var(--paper); }
  .envelope__contact {
    position: absolute; right: 30px; bottom: 22px; text-align: right; color: var(--paper);
    font-size: 9px; line-height: 1.55;
  }

  /* Business cards */
  .card {
    position: absolute; top: 600px; width: 230px; height: 140px; background: var(--orange);
    box-shadow: 0 6px 14px rgba(0,0,0,.25); color: var(--paper); overflow: hidden;
  }
  .card--front { left: 670px; display: flex; flex-direction: column; align-items: center; justify-content: center; gap: 12px; }
  .card--front .brand-square { width: 34px; height: 34px; }
  .card--front .brand-name { font-size: 11px; }
  .card--back { left: 910px; padding: 18px; }
  .card--back .card__name { position: absolute; right: 16px; top: 16px; }
  .card--back .card__name .brand-name { font-size: 8px; }
  .card__person { font-size: 9px; font-weight: 600; margin-top: 18px; }
  .card__role { font-size: 7px; margin-bottom: 8px; }
  .card__details { font-size: 7px; line-height: 1.55; }
  .card__accent { position: absolute; right: -20px; bottom: -20px; width: 100px; height: 100px; background: var(--orange-soft); opacity: .8; }
</style>
</head>
<body>
<main class="canvas">

  <section class="cover" aria-label="Report cover">
    <div class="cover__band">
      <div class="brand-lockup"><span class="brand-square"></span><span class="brand-name">Velvet Harbor</span></div>
    </div>
    <div class="cover__body">
      <span class="brand-square"></span>
      <span class="brand-name">Velvet Harbor</span>
    </div>
  </section>

  <section class="letterhead" aria-label="Letterhead">
    <header class="letterhead__header">
      <div class="brand-lockup"><span class="brand-square"></span><span class="brand-name">Velvet Harbor</span></div>
    </header>
    <div class="letterhead__body">
      <p>Dear Partner, thank you for your continued trust in our group. We are pleased to confirm the next steps for the new franchise locations and the opening schedule agreed during our recent meeting.</p>
      <p>Our kitchen teams will complete training over the coming weeks, and each site will receive a full supply plan, a staffing guide and a quality checklist before the first service day.</p>
      <p>We will share monthly reports on sales, guest feedback and food safety so that both sides can follow progress clearly and act quickly on anything that needs attention.</p>
      <p>Please review the attached terms and return a signed copy at your earliest convenience. Our office is available for any questions you may have.</p>
      <p>Kind regards, Operations Team</p>
    </div>
    <footer class="letterhead__footer"><span class="brand-name">Velvet Harbor</span></footer>
  </section>

  <section class="disc" aria-label="Disc label">
    <div class="disc__label"><span class="brand-name">Velvet Harbor</span></div>
    <div class="disc__hub"></div>
    <div class="disc__hole"></div>
    <span class="disc__mark"></span>
  </section>

  <section class="envelope" aria-label="Envelope">
    <div class="envelope__back"></div>
    <div class="envelope__front">
      <div class="envelope__name"><span class="brand-name">Velvet Harbor</span></div>
      <span class="envelope__mark"></span>
      <address class="envelope__contact" style="font-style:normal">
        Office: +000 4 555 0142<br>
        Mobile: +000 50 555 0187<br>
        Email: hello@velvetharbor.com<br>
        P.O. Box 2041, Harbor City<br>
        www.velvetharbor.com
      </address>
    </div>
  </section>

  <section class="card card--front" aria-label="Business card front">
    <span class="brand-square"></span>
    <span class="brand-name">Velvet Harbor</span>
  </section>

  <section class="card card--back" aria-label="Business card back">
    <span class="card__accent"></span>
    <div class="card__name"><span class="brand-name">Velvet Harbor</span></div>
    <p class="card__person">Daniel Morgan</p>
    <p class="card__role">Franchise Director</p>
    <p class="card__details">Office: +000 4 555 0142<br>Mobile: +000 50 555 0187<br>hello@velvetharbor.com</p>
  </section>

</main>
</body>
</html>
```